Start-up braucht modernes/hochwertiges Getränkeetikett
Zielgruppe
Wir sind ein modernes, nachhaltiges Start-up, welches eine neue Getränkekategorie auf den Markt bringt. Ein sogenanntes Elektrolyt-Getränk mit dem Namen FLUXO4. Es ist abgefüllt in eine 500 ml Flasche und enthält Magnesium, Kalzium, Kalium, und Natrium. Diese Stoffe (Elektrolyte) dienen der körperlichen Hydrierung. Zu Dehydrierung kann es durch Hitze, Alkohol, Sport oder Krankheit kommen. Krankheit liegt bei uns allerdings nicht im Fokus. In unserer Zielgruppe befinden sich hauptsächlich Personen im Alter von 18 - 29 Jahren.
Die Geschmacksrichtung ist Zitrone-Limette.
Aufgabenstellung
Das Etikett soll:
- MODERN, SCHLICHT und HOCHWERTIG sein, so dass es im Supermarkt hervorsticht
- erkenntlich machen, dass die Stoffe Magnesium, Natrium, Kalzium und Kalium enthalten sind
- sich farblich deutlich von der Farbe des Inhalts (weiß) abheben. (Vorzugsweise mit einem hellen Blau, türkis)
- für unsere junge Zielgruppe ansprechend sein
- ebenfalls auf die Geschmacksrichtung (Zitrone-Limette) hinweisen, und zwar so, dass wenn man eine weitere Geschmacksrichtung auf den Markt bringen möchte, diese leicht angepasst werden kann.
- nicht nach einem Energydrink oder einem typischen Sportgetränk aussehen
- unter dem Namen den Slogan 'Elektrolyt-Getränk' stehen haben
-Das Etikett ist nicht dursichtig sondern besteht aus Papier
Der Name sowie das Logo können selbstverständlich farblich verändert werden. Bei dem Logo können auch größere Änderungen vollzogen werden.
Bitte beachten Sie die unten zu stehenden Regler um sich einen guten Überblick über unsere Vorstellungen zu verschaffen. Die Platzierung des EAN-Code ist für ihr Design irrelevat .
Bei Unklarheiten gerne nachfragen!

```html
<!DOCTYPE html>
<html lang="de">
<head>
<meta charset="utf-8">
<title>FLUXO4 Elektrolyte – Etiketten</title>
<link rel="stylesheet" href="https://fonts.googleapis.com/css2?family=Jost:wght@300;400;600;800&family=Bebas+Neue&display=swap">
<style>
  :root {
    --navy: #0c1a72;
    --blue: #1c3fc0;
    --blue-light: #3d86ea;
    --night: #03061a;
    --white: #ffffff;
    --ink: #1a1a1a;
    --apple: #c9da3b;
    --peach: #da760f;
    --peach-deep: #cf6a08;
    --lemon: #f8c700;
    --mineral-warm: #f0a24a;
    --mineral-cool: #a9d36a;
  }
  * { box-sizing: border-box; margin: 0; padding: 0; }
  html, body { width: 1200px; height: 1039px; overflow: hidden; background: var(--white); }
  .canvas { position: relative; width: 1200px; height: 1039px; }

  .label {
    position: absolute; top: 305px; width: 312px; height: 460px; overflow: hidden;
    font-family: "Jost", sans-serif; color: var(--white);
  }
  .label--apple { left: 57px; --accent: var(--apple); }
  .label--peach { left: 459px; --accent: linear-gradient(180deg, var(--peach-deep), var(--peach)); }
  .label--lemon { left: 846px; --accent: var(--lemon); }

  .label__field {
    position: absolute; inset: 0 0 32px 0;
    background:
      linear-gradient(180deg, rgba(3,6,26,0) 55%, rgba(3,6,26,0.85) 78%, var(--night) 95%),
      radial-gradient(ellipse 70% 55% at 50% 32%, var(--blue-light) 0%, var(--blue) 40%, var(--navy) 80%);
  }

  .label__wedge {
    position: absolute; top: 0; left: 65px; width: 182px; height: 107px;
    background: var(--accent);
    clip-path: polygon(0 0, 100% 0, 50% 100%);
  }
  .brand {
    position: absolute; top: 7px; left: 0; width: 100%; text-align: center;
    font-family: "Jost", sans-serif; font-weight: 800; font-size: 27px; letter-spacing: 0.5px;
    color: var(--white); line-height: 1;
  }
  .category {
    position: absolute; top: 127px; left: 0; width: 100%; text-align: center;
    font-family: "Bebas Neue", sans-serif; font-weight: 400; font-size: 39px; letter-spacing: 8.5px; padding-left: 8px; line-height: 1;
  }
  .benefits {
    position: absolute; top: 163px; left: 33px; list-style: none;
    font-weight: 400; font-size: 16.5px; line-height: 19.8px;
  }
  .minerals {
    position: absolute; top: 171px; left: 180px; width: 80px; height: 80px; border-radius: 50%;
    border: 3px solid var(--white);
    background: radial-gradient(circle at 40% 35%, var(--mineral-warm) 0%, var(--mineral-cool) 100%);
  }
  .claim {
    position: absolute; top: 272px; left: 0; width: 100%; text-align: center; line-height: 1;
  }
  .claim__zero { display: block; font-weight: 800; font-size: 21px; }
  .claim__text { display: block; margin-top: 6px; font-weight: 300; font-size: 21px; }
  .flavour-art {
    position: absolute; top: 323px; left: 88px; width: 126px; height: 105px;
    background: radial-gradient(ellipse at 50% 55%, rgba(255,255,255,0.28) 0%, rgba(255,255,255,0.08) 60%, rgba(255,255,255,0) 75%);
  }
  .flavour {
    position: absolute; left: 0; bottom: 0; width: 100%; height: 32px;
    background: var(--accent); color: var(--ink);
    display: flex; align-items: center; justify-content: center;
    font-weight: 400; font-size: 18px; letter-spacing: 0.3px;
  }
</style>
</head>
<body>
<main class="canvas">
  <section class="label label--apple">
    <div class="label__field" role="img" aria-label="Blauer Hintergrund mit Punktmuster"></div>
    <div class="label__wedge"></div>
    <p class="brand">FLUXO4</p>
    <h2 class="category">ELEKTROLYTE</h2>
    <ul class="benefits"><li>Mehr Ausdauer</li><li>Mehr Konzentration</li><li>100% natürliche</li><li>Inhaltsstoffe</li></ul>
    <div class="minerals" role="img" aria-label="Grafik der Mineralstoffe Magnesium, Kalzium, Kalium, Natrium"></div>
    <p class="claim"><span class="claim__zero">ZERO</span><span class="claim__text">Calorie &amp; Sugar</span></p>
    <div class="flavour-art" role="img" aria-label="Linienzeichnung von Äpfeln"></div>
    <p class="flavour">APFEL</p>
  </section>

  <section class="label label--peach">
    <div class="label__field" role="img" aria-label="Blauer Hintergrund mit Punktmuster"></div>
    <div class="label__wedge"></div>
    <p class="brand">FLUXO4</p>
    <h2 class="category">ELEKTROLYTE</h2>
    <ul class="benefits"><li>Mehr Ausdauer</li><li>Mehr Konzentration</li><li>100% natürliche</li><li>Inhaltsstoffe</li></ul>
    <div class="minerals" role="img" aria-label="Grafik der Mineralstoffe Magnesium, Kalzium, Kalium, Natrium"></div>
    <p class="claim"><span class="claim__zero">ZERO</span><span class="claim__text">Calorie &amp; Sugar</span></p>
    <div class="flavour-art" role="img" aria-label="Linienzeichnung von Pfirsichen"></div>
    <p class="flavour">PEACH</p>
  </section>

  <section class="label label--lemon">
    <div class="label__field" role="img" aria-label="Blauer Hintergrund mit Punktmuster"></div>
    <div class="label__wedge"></div>
    <p class="brand">FLUXO4</p>
    <h2 class="category">ELEKTROLYTE</h2>
    <ul class="benefits"><li>Mehr Ausdauer</li><li>Mehr Konzentration</li><li>100% natürliche</li><li>Inhaltsstoffe</li></ul>
    <div class="minerals" role="img" aria-label="Grafik der Mineralstoffe Magnesium, Kalzium, Kalium, Natrium"></div>
    <p class="claim"><span class="claim__zero">ZERO</span><span class="claim__text">Calorie &amp; Sugar</span></p>
    <div class="flavour-art" role="img" aria-label="Linienzeichnung von Zitrone und Limette"></div>
    <p class="flavour">ZITRONE/LIMETTE</p>
  </section>
</main>
</body>
</html>
```